Business Card for a Dental Office

The design should communicate integrity, quality and reliability. We also want the card look elegant, simple, but still stand out, different from the traditional-dental-office business card.

Industry/Entity Type

Business

```html
<!DOCTYPE html>
<html lang="en">
<head>
<meta charset="utf-8">
<title>Larkfield Dental Centre – Business Card</title>
<link href="https://fonts.googleapis.com/css2?family=Source+Sans+3:wght@400;600&display=swap" rel="stylesheet">
<style>
  :root{
    --backdrop:#000000;
    --card:#36373b;
    --card-edge:#2f3034;
    --gold:#e2c21c;
    --gold-deep:#b89a12;
    --white:#ffffff;
  }
  html,body{margin:0;padding:0;width:1200px;height:900px;overflow:hidden;background:var(--backdrop);}
  body{position:relative;font-family:"Source Sans 3",sans-serif;color:var(--white);}
  .card{
    position:absolute;top:271px;width:457px;height:281px;border-radius:14px;
    background:radial-gradient(ellipse at 50% 40%,var(--card) 0%,var(--card-edge) 100%);
  }
  .card--front{left:137px;}
  .card--back{left:626px;}

  .brand-mark{position:absolute;display:flex;align-items:center;gap:10px;}
  .brand-mark__square{width:34px;height:34px;background:var(--gold);flex:none;}
  .brand-mark__name{font-weight:600;color:var(--white);line-height:1.05;}

  .card--front .brand-mark{left:58px;top:112px;width:170px;}
  .card--front .brand-mark__name{font-size:19px;}

  .divider{position:absolute;left:232px;top:70px;width:1px;height:145px;background:var(--gold-deep);}

  .contact{position:absolute;left:247px;top:68px;}
  .contact__name{margin:0;font-size:18.5px;font-weight:400;color:var(--gold);line-height:1;}
  .contact__role{margin:5px 0 0;font-size:12.5px;line-height:1;}
  .contact__address{margin:15px 0 0;font-size:12.5px;line-height:16px;font-style:normal;}
  .contact__list{list-style:none;margin:10px 0 0;padding:0;font-size:12.5px;}
  .contact__list li{display:flex;align-items:center;gap:6px;height:16.5px;}
  .contact__list svg{width:10px;height:10px;flex:none;fill:var(--gold);}

  .card--back .brand-lockup{position:absolute;left:75px;top:104px;}
  .card--back .brand-mark{position:static;}
  .card--back .brand-mark__square{width:38px;height:38px;}
  .card--back .brand-mark__name{font-size:23px;letter-spacing:.3px;text-transform:uppercase;}
  .tagline{margin:3px 0 0 48px;font-size:10.5px;font-weight:600;letter-spacing:.6px;text-transform:uppercase;color:var(--gold);}
</style>
</head>
<body>

<section class="card card--front" aria-label="Card front">
  <div class="brand-mark">
    <span class="brand-mark__square"></span>
    <span class="brand-mark__name">Larkfield Dental</span>
  </div>
  <div class="divider"></div>
  <div class="contact">
    <h1 class="contact__name">Daniel Hart</h1>
    <p class="contact__role">Managing Director</p>
    <address class="contact__address">48, Orchard Lane<br>Westbury, 204518.</address>
    <ul class="contact__list">
      <li><svg viewBox="0 0 10 10"><path d="M2 0.5 3.6 2.6 2.7 3.6c.6 1.4 1.7 2.5 3.1 3.1l1-.9L9.5 7.5 8.6 9.3C4.4 9 1 5.6.7 1.4z"/></svg>044-555 210 384</li>
      <li><svg viewBox="0 0 10 10"><path d="M0 2h10v6H0z M0 2l5 3.3L10 2" /><path d="M0 2l5 3.3L10 2v.9L5 6.2 0 2.9z" fill="#36373b"/></svg>info@larkfielddental.com</li>
      <li><svg viewBox="0 0 10 10"><path d="M4.2 5.8 5.8 4.2M3.5 4.6 1.9 6.2a1.4 1.4 0 0 0 1.9 1.9L5.4 6.5M6.5 5.4 8.1 3.8a1.4 1.4 0 0 0-1.9-1.9L4.6 3.5" fill="none" stroke="#e2c21c" stroke-width="1.2" stroke-linecap="round"/></svg>www.larkfielddental.com</li>
    </ul>
  </div>
</section>

<section class="card card--back" aria-label="Card back">
  <div class="brand-lockup">
    <div class="brand-mark">
      <span class="brand-mark__square"></span>
      <span class="brand-mark__name">Larkfield Dental Centre</span>
    </div>
    <p class="tagline">Your smile is your gift to others</p>
  </div>
</section>

</body>
</html>
```